Kelvaro.ch is looking for business card letterhead and envelope C5 with WOW effect

We need a strong business card for our company Kelvaro.ch, logo is available. You want a black or dark background on which the logo Stark r% 26 # 252; appears. Letterhead and envelope in C5 format should be in a similar design, but does not have to be We need a strong business card for our company Kelvaro.ch, logo is available. A black or dark background is desired, on which the logo Stark comes across. The letterhead and the envelope in C5 format should have a similar design.

Target Market(s)

Private customers as well as entrepreneurs

Contact Information for Business Card

E-mail: info@kelvaro-example.ch
Web.www.Kelvaro-example.ch
Tel: +41 ( 0 ) 79 482 6037
Adresse:
Lindenweg 14
9406 Tarnbach

Hier kann man Icons verwenden für Email,Tel und Adressse

Font styles to use
Other font styles liked:
• Dubai,bold

Colors

Designer to choose colors to be used in the design.

Requirements
Must have
• WOW effect
Nice to have
• R% 26 # 252; back business card with our service listings. - VEHICLE LABELING - SHOP WINDOW LABELING - STICKERS AND MUCH MORE ... in red color

```html
<!DOCTYPE html>
<html lang="en">
<head>
<meta charset="utf-8">
<title>Kelvaro.ch – Business Card</title>
<link rel="stylesheet" href="https://fonts.googleapis.com/css2?family=Hind:wght@500;600&family=Saira:wght@700&display=swap">
<style>
  :root {
    --page-bg: #8c8c8c;
    --card-deep: #171d33;
    --card-mid: #1f2f66;
    --card-glow: #2f5fc4;
    --accent-yellow: #f6c12c;
    --brand-white: #ffffff;
    --frame-fill: rgba(12, 18, 40, 0.55);
  }
  * { box-sizing: border-box; margin: 0; padding: 0; }
  html, body {
    width: 1200px; height: 1200px; overflow: hidden;
    background: var(--page-bg);
  }
  .card {
    position: absolute; left: 250px; width: 700px; height: 400px;
    border-radius: 18px; overflow: hidden;
  }
  .card--front { top: 190px; }
  .card--back { top: 610px; height: 398px; }
  .card__backdrop {
    position: absolute; inset: 0;
    background:
      radial-gradient(circle at 45% 45%, rgba(47, 95, 196, 0.65) 0%, rgba(47, 95, 196, 0) 45%),
      radial-gradient(circle at 80% 20%, rgba(47, 95, 196, 0.35) 0%, rgba(47, 95, 196, 0) 35%),
      linear-gradient(135deg, var(--card-deep) 0%, var(--card-mid) 55%, var(--card-deep) 100%);
  }
  .brand {
    position: absolute; display: flex; align-items: center;
  }
  .brand__dot {
    border-radius: 50%; background: var(--accent-yellow);
  }
  .brand__name {
    font-family: "Saira", "Hind", sans-serif; font-weight: 700;
    color: var(--brand-white); letter-spacing: 1px; line-height: 1;
  }
  .card--front .brand { left: 110px; top: 100px; gap: 56px; }
  .card--front .brand__dot { width: 150px; height: 150px; }
  .card--front .brand__name { font-size: 46px; }
  .card--back .brand { left: 190px; top: 58px; gap: 30px; }
  .card--back .brand__dot { width: 100px; height: 100px; }
  .card--back .brand__name { font-size: 31px; }

  .contact {
    position: absolute; width: 265px; height: 30px;
    display: flex; align-items: center; justify-content: center; gap: 10px;
    font-family: "Hind", sans-serif; font-weight: 600; font-size: 19px;
    color: var(--accent-yellow);
  }
  .contact__frame {
    position: absolute; inset: 0; width: 100%; height: 100%;
  }
  .contact__frame polygon {
    fill: var(--frame-fill); stroke: var(--accent-yellow); stroke-width: 1.6;
  }
  .contact__icon, .contact__text { position: relative; }
  .contact__icon { width: 22px; height: 22px; flex: none; }
  .contact--web   { left: 85px;  top: 287px; }
  .contact--mail  { left: 85px;  top: 325px; }
  .contact--phone { left: 350px; top: 265px; }
  .contact--street{ left: 350px; top: 305px; }
  .contact--city  { left: 350px; top: 345px; }
</style>
</head>
<body>

<section class="card card--front">
  <div class="card__backdrop" role="img" aria-label="Dark blue glowing network of connected dots and lines"></div>
  <div class="brand">
    <span class="brand__dot"></span>
    <span class="brand__name">KELVARO.CH</span>
  </div>
</section>

<section class="card card--back">
  <div class="card__backdrop" role="img" aria-label="Dark blue glowing network of connected dots and lines"></div>
  <div class="brand">
    <span class="brand__dot"></span>
    <span class="brand__name">KELVARO.CH</span>
  </div>

  <div class="contact contact--web">
    <svg class="contact__frame" viewBox="0 0 265 30" preserveAspectRatio="none"><polygon points="12,1 253,1 264,15 253,29 12,29 1,15"/></svg>
    <svg class="contact__icon" viewBox="0 0 22 22"><circle cx="11" cy="11" r="10" fill="#3a3f4f" stroke="#f6c12c" stroke-width="1"/><circle cx="11" cy="11" r="6" fill="none" stroke="#c9c9c9" stroke-width="1"/><ellipse cx="11" cy="11" rx="2.5" ry="6" fill="none" stroke="#c9c9c9" stroke-width="1"/><line x1="5" y1="11" x2="17" y2="11" stroke="#c9c9c9" stroke-width="1"/></svg>
    <span class="contact__text">www.Kelvaro-example.ch</span>
  </div>

  <div class="contact contact--mail">
    <svg class="contact__frame" viewBox="0 0 265 30" preserveAspectRatio="none"><polygon points="12,1 253,1 264,15 253,29 12,29 1,15"/></svg>
    <svg class="contact__icon" viewBox="0 0 22 22"><circle cx="11" cy="11" r="10" fill="#f6c12c"/><rect x="5.5" y="7" width="11" height="8" fill="#1b2140"/><polyline points="5.5,7 11,11.5 16.5,7" fill="none" stroke="#f6c12c" stroke-width="1"/></svg>
    <span class="contact__text">info@kelvaro-example.ch</span>
  </div>

  <div class="contact contact--phone">
    <svg class="contact__frame" viewBox="0 0 265 30" preserveAspectRatio="none"><polygon points="12,1 253,1 264,15 253,29 12,29 1,15"/></svg>
    <svg class="contact__icon" viewBox="0 0 22 22"><circle cx="11" cy="11" r="10" fill="#f6c12c"/><path d="M5 9 q6 -5 12 0 l-1.5 2 h-2 v-1.5 h-5 v1.5 h-2 z" fill="#1b2140"/><rect x="7" y="12" width="8" height="4" rx="1" fill="#1b2140"/></svg>
    <span class="contact__text">+41 ( 0 ) 79 482 6037</span>
  </div>

  <div class="contact contact--street">
    <svg class="contact__frame" viewBox="0 0 265 30" preserveAspectRatio="none"><polygon points="12,1 253,1 264,15 253,29 12,29 1,15"/></svg>
    <svg class="contact__icon" viewBox="0 0 22 22"><circle cx="11" cy="11" r="10" fill="none" stroke="#f6c12c" stroke-width="1.4"/><path d="M11 5 a3.5 3.5 0 0 1 3.5 3.5 c0 2.5 -3.5 6 -3.5 6 s-3.5 -3.5 -3.5 -6 A3.5 3.5 0 0 1 11 5 z" fill="none" stroke="#f6c12c" stroke-width="1.2"/><circle cx="11" cy="8.5" r="1.2" fill="#f6c12c"/><ellipse cx="11" cy="16" rx="4" ry="1.2" fill="none" stroke="#f6c12c" stroke-width="1"/></svg>
    <span class="contact__text">Lindenweg 14</span>
  </div>

  <div class="contact contact--city">
    <svg class="contact__frame" viewBox="0 0 265 30" preserveAspectRatio="none"><polygon points="12,1 253,1 264,15 253,29 12,29 1,15"/></svg>
    <span class="contact__text">9406 Tarnbach</span>
  </div>
</section>

</body>
</html>
```